Independent Financial Advisor Billboard Campaign - Maple Crest Financial

I am a local, independent financial advisor. My company is Maple Crest Financial, located in Charleston, WV. My main source of revenue comes from those nearing or entering retirement that need assistance with financial planning and investment management. Many are looking to rollover their employer retirement plan into an IRA account. I would like a billboard design campaign that focuses on this type of client. Please see our website www.maplecrestfinancial.com for more information.

```html
<!DOCTYPE html>
<html lang="en">
<head>
<meta charset="utf-8">
<title>Maple Crest Financial – Retirement Billboard</title>
<link href="https://fonts.googleapis.com/css2?family=Poppins:wght@600;700;800&display=swap" rel="stylesheet">
<style>
  :root {
    --navy: #0c2650;
    --navy-deep: #071b3d;
    --bright-blue: #2f86e8;
    --white: #ffffff;
    --backdrop: #d2d2d2;
    --photo-light: #e9edf2;
    --photo-mid: #c9b4a3;
  }
  html, body {
    margin: 0;
    padding: 0;
    width: 1066px;
    height: 1200px;
    overflow: hidden;
    background: var(--backdrop);
  }
  .canvas {
    position: relative;
    width: 1066px;
    height: 1200px;
  }
  .billboard {
    position: absolute;
    left: 33px;
    top: 436px;
    width: 1000px;
    height: 327px;
    overflow: hidden;
    background: radial-gradient(ellipse at 35% 40%, #12315f 0%, var(--navy) 45%, var(--navy-deep) 100%);
    box-shadow: 8px 8px 10px rgba(0,0,0,0.35);
    font-family: "Poppins", sans-serif;
  }
  .headline {
    position: absolute;
    left: 46px;
    top: 40px;
    margin: 0;
    font-weight: 800;
    font-size: 110px;
    line-height: 91px;
    letter-spacing: -2.5px;
    white-space: nowrap;
    text-transform: uppercase;
    z-index: 2;
  }
  .headline-accent { display: block; color: var(--bright-blue); }
  .headline-main { display: block; color: var(--white); }
  .contact-row {
    position: absolute;
    left: 50px;
    top: 250px;
    height: 42px;
    display: flex;
    align-items: center;
    gap: 22px;
    z-index: 2;
  }
  .phone {
    color: var(--white);
    font-weight: 700;
    font-size: 40px;
    letter-spacing: -0.5px;
    line-height: 1;
  }
  .divider {
    width: 2px;
    height: 42px;
    background: var(--bright-blue);
  }
  .brand {
    display: flex;
    align-items: center;
    gap: 12px;
  }
  .brand-square {
    width: 30px;
    height: 30px;
    background: var(--white);
  }
  .brand-name {
    color: var(--white);
    font-weight: 600;
    font-size: 18px;
    line-height: 19px;
    letter-spacing: 0.6px;
    text-transform: uppercase;
  }
  .advisor-photo {
    position: absolute;
    left: 757px;
    top: 28px;
    width: 227px;
    height: 299px;
    border-radius: 80px 80px 0 0;
    background: linear-gradient(180deg, var(--photo-mid) 0%, var(--photo-mid) 28%, var(--photo-light) 42%, var(--photo-light) 100%);
    z-index: 1;
  }
  .web-pill {
    position: absolute;
    left: 574px;
    top: 249px;
    width: 426px;
    height: 39px;
    border-radius: 20px 0 0 20px;
    background: var(--bright-blue);
    color: var(--white);
    font-weight: 700;
    font-size: 20px;
    line-height: 39px;
    padding-left: 20px;
    box-sizing: border-box;
    letter-spacing: 0.5px;
    white-space: nowrap;
    z-index: 3;
  }
</style>
</head>
<body>
<div class="canvas">
  <section class="billboard">
    <h1 class="headline">
      <span class="headline-accent">Retirement</span>
      <span class="headline-main">Done Right!</span>
    </h1>
    <div class="contact-row">
      <span class="phone">304.555.0142</span>
      <span class="divider"></span>
      <div class="brand">
        <span class="brand-square"></span>
        <span class="brand-name">Maple Crest<br>Financial</span>
      </div>
    </div>
    <div class="advisor-photo" role="img" aria-label="Portrait photo of the financial advisor in a white polo shirt"></div>
    <div class="web-pill">www.maplecrestfinancial.com</div>
  </section>
</div>
</body>
</html>
```